TK Stationery - Modern Contemporary

Develop modern template for Letterhead and Stationery (business card, letterhead, envelopes) using the TK Logo and Icon

Colors
0054AA
0677BA
7BADD7
CADEEF
E8F1F8
00AB8E
00BBA5
67D7C9
C6EFE9
E9F9F6
EE7325
F08F49
F5BC92
FAE3D3
FDF4ED
6B429C
8869AF
B7A5CE
E3DAEB
F3F0F8

```html
<!DOCTYPE html>
<html lang="en">
<head>
<meta charset="utf-8">
<title>TK Stationery</title>
<link href="https://fonts.googleapis.com/css2?family=Open+Sans:wght@400;600&family=Lato:wght@400&display=swap" rel="stylesheet">
<style>
  :root {
    --navy: #2b2f4a;
    --green: #1fbf74;
    --paper: #ffffff;
    --ink: #444a55;
    --ink-dark: #1f2233;
    --peach: #f5bc92;
    --rule: #eceef0;
    --backdrop: #e6e8eb;
  }
  html, body { margin: 0; padding: 0; overflow: hidden; }
  body {
    width: 1200px; height: 1200px; position: relative;
    background: var(--backdrop);
    font-family: "Open Sans", Arial, sans-serif;
    color: var(--ink);
  }
  .sheet { position: absolute; background: var(--paper); box-shadow: 0 2px 10px rgba(0,0,0,.12); }
  .band { position: absolute; left: 0; width: 100%; display: block; }
  .brand-name {
    position: absolute; margin: 0; white-space: nowrap;
    font-family: "Open Sans", Arial, sans-serif; font-weight: 400;
    color: var(--navy); letter-spacing: .5px; line-height: 1;
  }

  /* Letterhead */
  .letterhead { left: 119px; top: 278px; width: 556px; height: 716px; }
  .letterhead .band-top { top: 0; height: 14px; }
  .letterhead .band-bottom { bottom: 0; height: 9px; }
  .letterhead .brand-name { top: 17px; left: 0; width: 100%; text-align: center; font-size: 30px; }
  .letter-text { position: absolute; left: 52px; right: 54px; margin: 0; font-size: 8.8px; }
  .meta { line-height: 10.8px; }
  .issue-date { top: 134px; }
  .recipient { top: 265px; top: 155px; }
  .salutation { top: 218px; }
  .paragraph { line-height: 16px; text-align: justify; }
  .para-one { top: 247px; }
  .para-two { top: 343px; }
  .para-three { top: 407px; }
  .closing { top: 490px; }
  .signature-mark {
    position: absolute; left: 52px; top: 510px; width: 128px; height: 14px;
    background: linear-gradient(90deg, rgba(68,74,85,.18), rgba(68,74,85,.05)); border-radius: 3px;
  }
  .signer-name { top: 534px; font-size: 10.4px; color: var(--ink-dark); line-height: 14px; }
  .signer-role { top: 553px; line-height: 12px; }
  .letter-footer {
    position: absolute; left: 0; right: 0; top: 664px;
    text-align: center; font-size: 10.2px; color: var(--ink-dark); line-height: 15px;
  }
  .footer-address { display: inline-block; width: 321px; border-bottom: 1px solid var(--peach); }
  .footer-contact { margin-top: 2px; }
  .accent { color: var(--green); }

  /* Envelope front */
  .envelope-front { left: 715px; top: 492px; width: 432px; height: 217px; }
  .envelope-front .band-top { top: 0; height: 9px; }
  .envelope-front .band-bottom { bottom: 0; height: 10px; }
  .envelope-front .brand-name { left: 26px; top: 16px; font-size: 21px; }
  .return-address {
    position: absolute; left: 26px; right: 26px; top: 184px;
    font-family: "Lato", Arial, sans-serif; font-size: 8px; line-height: 10px;
    color: var(--ink-dark); border-top: 1px solid var(--rule); padding-top: 6px;
  }

  /* Envelope back */
  .envelope-back { left: 717px; top: 743px; width: 429px; height: 213px; }
  .envelope-back .flap { position: absolute; top: 0; left: 0; width: 100%; height: 50px; }
</style>
</head>
<body>

<section class="sheet letterhead">
  <svg class="band band-top" viewBox="0 0 556 14" preserveAspectRatio="none" aria-hidden="true">
    <polygon points="0,0 282,0 279,14 0,14" fill="var(--navy)"/>
    <polygon points="285,0 556,0 556,14 282,14" fill="var(--green)"/>
  </svg>
  <h1 class="brand-name">tallis kora</h1>

  <p class="letter-text meta issue-date">Issuing Date: May 5, 2018</p>
  <p class="letter-text meta recipient">Name Of Employee Mr. XYZABC<br>Address of Employee<br>Address Line 2 etc..</p>
  <p class="letter-text meta salutation">Dear Mr.XYZABC</p>
  <p class="letter-text paragraph para-one">Lorem Ipsum has been the industry's standard dummy text ever since the 1500s, when an unknown printer took a galley of type and scrambled it to make a type specimen book. It has survived not only five centuries, but also the leap into electronic typesetting, remaining essentially unchanged. It was popularised in the 1960s with the release of Typeline sheets containing Lorem Ipsum passages, and more recently with desktop publishing software like Pressform Studio including versions of Lorem Ipsum.</p>
  <p class="letter-text paragraph para-two">Lorem Ipsum is simply dummy text of the printing and typesetting industry. Lorem Ipsum has been the industry's standard dummy text ever since the 1500s, when an unknown printer took a galley of type and scrambled it to make a type specimen book.</p>
  <p class="letter-text paragraph para-three">It has survived not only five centuries, but also the leap into electronic typesetting, remaining essentially unchanged. It was popularised in the 1960s with the release of Typeline sheets containing Lorem Ipsum passages.</p>
  <p class="letter-text meta closing">Yours Sincerely</p>
  <span class="signature-mark" role="img" aria-label="Handwritten signature of Daniel Reyes"></span>
  <p class="letter-text signer-name">Daniel Reyes</p>
  <p class="letter-text signer-role">Managing Director</p>

  <footer class="letter-footer">
    <div class="footer-address">18 Harbour Row, Portvale Country, 20817</div>
    <div class="footer-contact">P: 000-555 0100 | E: hello@examplemail.com | www.<span class="accent">tallis-kora</span>.com</div>
  </footer>

  <svg class="band band-bottom" viewBox="0 0 556 9" preserveAspectRatio="none" aria-hidden="true">
    <polygon points="0,0 277,0 274,9 0,9" fill="var(--navy)"/>
    <polygon points="280,0 556,0 556,9 277,9" fill="var(--green)"/>
  </svg>
</section>

<section class="sheet envelope-front">
  <svg class="band band-top" viewBox="0 0 432 9" preserveAspectRatio="none" aria-hidden="true">
    <polygon points="0,0 211,0 209,9 0,9" fill="var(--navy)"/>
    <polygon points="214,0 432,0 432,9 212,9" fill="var(--green)"/>
  </svg>
  <h2 class="brand-name">tallis kora</h2>
  <div class="return-address">18 Harbour Row, Portvale Country, 20817</div>
  <svg class="band band-bottom" viewBox="0 0 432 10" preserveAspectRatio="none" aria-hidden="true">
    <polygon points="0,0 217,0 214,10 0,10" fill="var(--navy)"/>
    <polygon points="220,0 432,0 432,10 217,10" fill="var(--green)"/>
  </svg>
</section>

<section class="sheet envelope-back">
  <svg class="flap" viewBox="0 0 429 50" preserveAspectRatio="none" aria-hidden="true">
    <polygon points="0,0 237,0 217,50 16,50" fill="var(--navy)"/>
    <polygon points="240,0 429,0 418,50 221,50" fill="var(--green)"/>
  </svg>
</section>

</body>
</html>
```